Business Card Design for company

We want new business cards. We'd like something different-- yet still highly professional. Our tagline is Providing leadership, delivering success. Stock photos are ok, as long as they are relevant and look upscale.

Target Market(s)

Architecture/Business Management Consulting/Engineering Consulting

Contact Information for Business Card

dark gray background with pops of blue might be good, but you tell me. You're the designers. Rounded corners might be nice, but again, you tell me.

Font styles to use
Serif
Sans Serif

Colors
3276b5
5c5c5c
9d9d9d
fbfbfb

Requirements
Nice to have
• Something different, but still very professional.

```html
<!DOCTYPE html>
<html lang="en">
<head>
<meta charset="utf-8">
<title>Norvale Partners – Business Cards</title>
<link href="https://fonts.googleapis.com/css2?family=Work+Sans:wght@400;500;600;700&display=swap" rel="stylesheet">
<style>
  :root {
    --stage: #2b2c2e;
    --card-dark: #474b52;
    --card-light: #fbfbfb;
    --brand-blue: #3276b5;
    --ink-dark: #5c5c5c;
    --ink-muted: #c9ccd1;
    --ink-white: #ffffff;
    --rule: #9d9d9d;
  }
  * { box-sizing: border-box; margin: 0; padding: 0; }
  html, body {
    width: 1200px; height: 900px; overflow: hidden;
    background: radial-gradient(ellipse at 50% 40%, #3a3b3e 0%, var(--stage) 70%);
    font-family: "Work Sans", Arial, sans-serif;
  }
  .stage {
    position: relative; width: 1200px; height: 900px;
    display: flex; flex-direction: column; align-items: center; justify-content: center; gap: 48px;
  }
  .card {
    position: relative; width: 600px; height: 343px; border-radius: 4px; overflow: hidden;
    box-shadow: 0 18px 40px rgba(0,0,0,.45);
  }

  /* Back side */
  .card-back { background: var(--card-dark); }
  .card-back .brand {
    position: absolute; left: 0; right: 0; top: 112px;
    display: flex; align-items: center; justify-content: center; gap: 14px;
  }
  .brand-square { width: 22px; height: 22px; background: var(--brand-blue); }
  .card-back .brand-name {
    color: var(--ink-white); font-weight: 600; font-size: 34px; letter-spacing: 4px; text-transform: uppercase;
  }
  .card-back .web-rule {
    position: absolute; left: 60px; right: 60px; top: 236px;
    display: flex; align-items: center; gap: 14px;
    color: var(--ink-white); font-size: 13px; letter-spacing: .5px;
  }
  .web-rule .line { flex: 1; height: 1px; background: var(--rule); opacity: .7; }

  /* Front side */
  .card-front { background: var(--card-dark); }
  .card-front .panel-light {
    position: absolute; left: 0; top: 0; bottom: 0; width: 262px; background: var(--card-light);
  }
  .card-front .notch { position: absolute; left: 262px; top: 54px; }
  .card-front .brand {
    position: absolute; left: 0; width: 262px; top: 150px;
    display: flex; align-items: center; justify-content: center; gap: 10px;
  }
  .card-front .brand-square { width: 16px; height: 16px; }
  .card-front .brand-name {
    color: var(--ink-dark); font-weight: 600; font-size: 22px; letter-spacing: 2.5px; text-transform: uppercase;
  }
  .contact { position: absolute; left: 304px; top: 54px; color: var(--ink-white); }
  .contact .name { font-weight: 600; font-size: 22px; letter-spacing: 1.5px; text-transform: uppercase; }
  .contact .role { font-size: 13px; color: var(--ink-muted); margin-top: 4px; }
  .contact .address { font-size: 13px; line-height: 1.5; margin-top: 26px; color: var(--ink-muted); }
  .contact .lines { list-style: none; margin-top: 18px; font-size: 13px; line-height: 1.75; }
  .contact .lines li { display: flex; align-items: center; gap: 9px; }
  .contact .lines svg { width: 11px; height: 11px; fill: var(--ink-muted); flex: none; }
  .contact .lines .web { font-weight: 600; font-size: 14px; }
</style>
</head>
<body>
<main class="stage">

  <section class="card card-back" aria-label="Business card back">
    <div class="brand">
      <span class="brand-square"></span>
      <span class="brand-name">Norvale Partners</span>
    </div>
    <div class="web-rule">
      <span class="line"></span>
      <span>www.norvalepartners.com</span>
      <span class="line"></span>
    </div>
  </section>

  <section class="card card-front" aria-label="Business card front">
    <div class="panel-light"></div>
    <svg class="notch" width="12" height="20" viewBox="0 0 12 20" aria-hidden="true">
      <polygon points="0,0 12,10 0,20" fill="#fbfbfb"/>
    </svg>
    <div class="brand">
      <span class="brand-square"></span>
      <span class="brand-name">Norvale Partners</span>
    </div>
    <div class="contact">
      <p class="name">Daniel Reyes</p>
      <p class="role">Director</p>
      <p class="address">128 Harbour Lane,<br>Wellington, NZ, 6011</p>
      <ul class="lines">
        <li><svg viewBox="0 0 24 24"><path d="M6.6 10.8a15 15 0 0 0 6.6 6.6l2.2-2.2c.3-.3.7-.4 1-.2 1.1.4 2.3.6 3.6.6.6 0 1 .4 1 1V20c0 .6-.4 1-1 1A17 17 0 0 1 3 4c0-.6.4-1 1-1h3.5c.6 0 1 .4 1 1 0 1.3.2 2.5.6 3.6.1.3 0 .7-.2 1z"/></svg>(555) 204-7180</li>
        <li><svg viewBox="0 0 24 24"><path d="M2 5h20v14H2zm2 2v.5l8 5 8-5V7zm0 3v7h16v-7l-8 5z"/></svg>hello@norvalepartners.com</li>
        <li class="web"><svg viewBox="0 0 24 24"><circle cx="12" cy="12" r="10"/></svg>www.norvalepartners.com</li>
      </ul>
    </div>
  </section>

</main>
</body>
</html>
```